Consulting company business cards

We have a base design, but would be willing to update. We have a new logo/"tag" that needs to be added. Current business card design is attached for reference into our "style."

Industry/Entity Type

Business

Contact Information for Business Card

Should contain name and title, office number, mobile number if appropriate, e-mail, website, physical address, and company logo.

Font styles to use
Other font styles liked:
• See current card design on KorvandBCard

Colors
0455a3
85acd3
aaaaaa

Requirements
Must have
• Our colors are navy blue, gray, and a lighter blue
Nice to have
• Design that I can easily drop in new names/titles as we hire employees.

```html
<!DOCTYPE html>
<html lang="en">
<head>
<meta charset="utf-8">
<title>Torbeck business card – front and back</title>
<link rel="stylesheet" href="https://fonts.googleapis.com/css2?family=Jost:wght@400;500;600&display=swap">
<style>
  :root {
    --navy: #0b3457;
    --navy-deep: #072a47;
    --light-blue: #85acd3;
    --band-light: #7fb0d2;
    --grey: #aaaaaa;
    --paper: #ffffff;
    --backdrop: #e4e6e9;
  }
  * { box-sizing: border-box; margin: 0; padding: 0; }
  html, body { width: 1200px; height: 900px; overflow: hidden; }
  body {
    background: var(--backdrop);
    font-family: "Jost", "Helvetica Neue", Arial, sans-serif;
    display: flex;
    flex-direction: column;
    align-items: center;
    justify-content: center;
    gap: 40px;
  }
  .card {
    position: relative;
    width: 640px;
    height: 366px;
    border-radius: 4px;
    overflow: hidden;
    box-shadow: 0 6px 18px rgba(0,0,0,0.18);
  }

  /* Front */
  .card-front { background: var(--paper); }
  .mascot-area {
    position: absolute;
    left: 40px; top: 112px;
    width: 240px; height: 220px;
    border-radius: 46% 40% 38% 44% / 42% 46% 40% 48%;
    background: radial-gradient(circle at 45% 40%, #8bbad9, var(--band-light));
  }
  .identity {
    position: absolute;
    left: 300px; top: 22px;
    color: var(--navy);
  }
  .identity .job-title { font-size: 17px; font-weight: 400; line-height: 1.1; }
  .identity .person-name { font-size: 22px; font-weight: 600; line-height: 1.2; }
  .contact-list { list-style: none; }
  .contact-band {
    position: absolute;
    right: 0;
    height: 46px;
    display: flex;
    align-items: center;
    gap: 12px;
    padding-left: 6px;
    border-radius: 23px 0 0 23px;
    color: var(--paper);
    font-size: 16px;
    font-weight: 500;
    line-height: 1.05;
  }
  .contact-band.is-navy { background: var(--navy); }
  .contact-band.is-light { background: var(--band-light); }
  .contact-icon {
    width: 34px; height: 34px;
    flex: none;
    display: flex; align-items: center; justify-content: center;
  }
  .contact-icon svg { width: 22px; height: 22px; fill: none; stroke: var(--paper); stroke-width: 1.8; stroke-linecap: round; stroke-linejoin: round; }
  .band-mobile  { top: 92px;  left: 290px; }
  .band-office  { top: 138px; left: 312px; }
  .band-email   { top: 184px; left: 334px; }
  .band-web     { top: 230px; left: 356px; }
  .band-address { top: 276px; left: 378px; }

  /* Back */
  .card-back {
    background: radial-gradient(ellipse at 50% 40%, var(--navy), var(--navy-deep));
    display: flex;
    flex-direction: column;
    align-items: center;
    justify-content: center;
    color: var(--paper);
  }
  .brand-name {
    font-family: "Jost", "Helvetica Neue", Arial, sans-serif;
    font-size: 88px;
    font-weight: 600;
    line-height: 1;
    color: var(--paper);
  }
  .brand-tagline {
    margin-top: 18px;
    font-size: 22px;
    font-weight: 400;
    letter-spacing: 5px;
    text-transform: uppercase;
  }
</style>
</head>
<body>

  <section class="card card-front" aria-label="Business card front">
    <div class="mascot-area" role="img" aria-label="Company mascot illustration: dog head in profile"></div>

    <div class="identity">
      <p class="job-title">Title</p>
      <p class="person-name">Name and Surname</p>
    </div>

    <ul class="contact-list">
      <li class="contact-band is-navy band-mobile">
        <span class="contact-icon"><svg viewBox="0 0 24 24"><rect x="7" y="2.5" width="10" height="19" rx="2"/><line x1="11" y1="18.5" x2="13" y2="18.5"/></svg></span>
        mobile number
      </li>
      <li class="contact-band is-light band-office">
        <span class="contact-icon"><svg viewBox="0 0 24 24"><path d="M6 3.5l3 .5 1.5 4-2 1.5a11 11 0 0 0 6 6l1.5-2 4 1.5.5 3c-.5 1.5-2 2.5-3.5 2.5C9.5 20.5 3.5 14.5 3.5 7 3.5 5.5 4.5 4 6 3.5z"/></svg></span>
        officce number
      </li>
      <li class="contact-band is-navy band-email">
        <span class="contact-icon"><svg viewBox="0 0 24 24"><rect x="3" y="5.5" width="18" height="13" rx="1.5"/><path d="M3.5 6.5l8.5 6.5 8.5-6.5"/></svg></span>
        e-mail
      </li>
      <li class="contact-band is-light band-web">
        <span class="contact-icon"><svg viewBox="0 0 24 24"><circle cx="12" cy="12" r="9"/><ellipse cx="12" cy="12" rx="4" ry="9"/><line x1="3" y1="12" x2="21" y2="12"/><path d="M5 7h14M5 17h14"/></svg></span>
        web site
      </li>
      <li class="contact-band is-navy band-address">
        <span class="contact-icon"><svg viewBox="0 0 24 24"><path d="M12 21.5s-6.5-6.5-6.5-11.5a6.5 6.5 0 0 1 13 0c0 5-6.5 11.5-6.5 11.5z"/><circle cx="12" cy="10" r="2.4"/></svg></span>
        physical<br>address
      </li>
    </ul>
  </section>

  <section class="card card-back" aria-label="Business card back">
    <h1 class="brand-name">Torbeck</h1>
    <p class="brand-tagline">A Cloud Consulting Company</p>
  </section>

</body>
</html>
```